Organic Infographic – "The 4 Dimensions of Transformation"

Overview:
We are a coaching/education brand (Brackwater Institute) and need a redesigned infographic illustrating our 4-area transformation model. Our current version (attached) uses a rigid, hard-edged triangle/pyramid layout — we want a completely new visual approach that feels organic, soft, and alive, since the topic is human personal development, not a technical process.

Content structure (please keep the wording, redesign the visual form):

4 areas: "Embodiment – The Foundation" and "Focus & Intuition Redefined – The Lens" sit on the same base level. "Heart Centered Living – The Bridge" sits one level above, connecting/enabling the other two. "Becoming Unlimited – The Peak" sits at the top, made possible by Heart Centered Living.
The 4 areas influence and inspire one another — this mutual connection must be visually recognizable (e.g. through overlapping zones, blended color transitions, connecting flowing lines, or similar). Areas may stay visually distinct; the connection between them is what must be shown.
Hierarchy should be expressed mainly through position/arrangement (ascending flow), not through size differences — all 4 areas should carry similar visual weight, since each is equally essential.
A supporting element: "The Brackwater Methodology" with 3 phases (Phase 1: Awareness & Insight, Phase 2: Integration & Practice, Phase 3: Expansion & Sustainable Growth), each with a short description (text provided below).

Style direction:
Organic, soft, flowing shapes — no sharp angles or rigid geometric triangles. Attached are 3 moodboard references showing the direction we like: overlapping/blended circular shapes, flowing ribbon-style connections, and organic swirl divisions. Please don't copy any of them directly — combine this organic/overlapping visual language with our specific asymmetric hierarchy (2 areas base level + 1 bridge + 1 peak), which none of the references show exactly. This creative translation is the core task.

Icons: Please design one new, unified icon per area (4 total) plus 3 simple icons for the methodology phases — consistent style across all 7, your creative interpretation is welcome.

Typography: Headlines in Arsenal, body text in DM Sans.

Colors: Base palette — Embodiment D09176, Focus & Intuition Redefined B6623E, Heart Centered Living D9866B, Becoming Unlimited 6F7A70, dark text 23211A, light accent EACEC1. Slight adjustments are welcome if they improve visual distinction between areas.

Technical requirements (important):

Final files as vector format (SVG, AI, or EPS), with separated, editable, non-flattened/non-merged layers and paths.
Shapes should consist of simple, closed outline paths — no fine textures, no complex multi-stop gradients, no photorealistic rendering — since the artwork will later be manually redrawn as a whiteboard-animation video.
Primary format: 16:9 landscape. A secondary vertical/mobile version (3 outer areas stacked below the top area) is welcome but optional.

Usage rights: Full commercial usage across website, video, and social media required.

Attachments to include: current draft PDF (for text content and logo reference only — not for layout), our logo file, and the 3 moodboard reference images.

Budget: $100–150 — please let us know if this realistically allows for more designer participation, or advise on adjusting scope/budget

Methodology phase texts (for the 3 supporting icons):

Phase 1: Awareness & Insight
Cultivating self-reflection, identifying patterns, and gaining clarity on personal drivers through introspective practices and data-informed assessment.

Phase 2: Integration & Practice
Applying tools and frameworks, developing new habits, and aligning actions with core values through consistent application and feedback loops.

Phase 3: Expansion & Sustainable Growth
Achieving long-term transformation, exceeding limitations, and fostering resilience through continuous evolution and a purpose-driven approach.

```html
<!DOCTYPE html>
<html lang="en">
<head>
<meta charset="utf-8">
<title>The 4 Dimensions of Transformation – Brackwater Institute</title>
<link rel="stylesheet" href="https://fonts.googleapis.com/css2?family=Arsenal:wght@400;700&family=DM+Sans:wght@400;700&display=swap">
<style>
  :root {
    --embodiment: #D09176;
    --focus: #B6623E;
    --heart: #D9866B;
    --peak: #6F7A70;
    --ink: #23211A;
    --accent: #EACEC1;
    --accent-soft: #F2DDD3;
    --paper: #FFFFFF;
    --stage: #F3F2F1;
    --on-color: #FBEDE6;
  }
  * { box-sizing: border-box; margin: 0; padding: 0; }
  html, body { width: 1066px; height: 1200px; overflow: hidden; }
  body { background: var(--stage); position: relative; font-family: "DM Sans", sans-serif; color: var(--ink); }

  .sheet { position: absolute; background: var(--paper); box-shadow: 0 2px 10px rgba(35,33,26,.08); transform-origin: 0 0; overflow: hidden; }
  .sheet--landscape { left: 20px; top: 20px; width: 1221px; height: 686px; transform: scale(0.84); }
  .sheet--portrait { left: 374px; top: 617px; width: 386px; height: 686px; transform: scale(0.82); }

  .abs { position: absolute; }
  .title-box { background: var(--accent); display: flex; align-items: center; justify-content: center; font-family: "Arsenal", sans-serif; font-weight: 700; color: var(--ink); box-shadow: 0 2px 4px rgba(35,33,26,.08); }
  .brand { display: flex; align-items: center; }
  .brand__dot { border-radius: 50%; background: var(--embodiment); flex: none; }
  .brand__name { font-family: "Arsenal", sans-serif; font-weight: 400; color: var(--embodiment); white-space: nowrap; }

  .links { position: absolute; left: 0; top: 0; overflow: visible; }
  .area { position: absolute; display: flex; flex-direction: column; align-items: center; justify-content: center; text-align: center; font-family: "Arsenal", sans-serif; font-weight: 700; color: var(--on-color); line-height: 1.05; }
  .area small { font-family: "DM Sans", sans-serif; font-weight: 400; color: var(--ink); line-height: 1.2; }
  .area--peak { background: var(--peak); }
  .area--heart { background: var(--heart); }
  .area--ground { background: var(--embodiment); }
  .area--lens { background: var(--focus); }

  .badge { position: absolute; background: var(--paper); border-style: solid; border-color: var(--accent); transform: rotate(45deg); display: flex; align-items: center; justify-content: center; }
  .badge__icon { border-radius: 50%; transform: rotate(-45deg); }
  .badge__icon--peak { background: var(--peak); }
  .badge__icon--heart { background: var(--heart); }
  .badge__icon--ground { background: var(--embodiment); }
  .badge__icon--lens { background: var(--focus); }

  .method-line { position: absolute; background: var(--peak); }
  .phase-tab { position: absolute; background: var(--peak); color: var(--on-color); font-family: "Arsenal", sans-serif; font-weight: 700; display: flex; align-items: center; justify-content: center; }
  .phase-card { position: absolute; background: var(--accent); box-shadow: 0 3px 8px rgba(35,33,26,.12); }
  .phase-card p { color: var(--ink); }
  .phase-card b { font-weight: 700; }
  .phase-icon { position: absolute; border-radius: 50%; background: var(--heart); border-style: solid; border-color: var(--accent-soft); }

  /* landscape sizing */
  .sheet--landscape .title-box { left: 32px; top: 30px; width: 565px; height: 70px; font-size: 34px; }
  .sheet--landscape .brand { left: 725px; top: 60px; gap: 12px; }
  .sheet--landscape .brand__dot { width: 74px; height: 74px; }
  .sheet--landscape .brand__name { font-size: 44px; }
  .sheet--landscape .area { width: 220px; height: 110px; border-radius: 55px; font-size: 21px; }
  .sheet--landscape .area small { font-size: 14px; margin-top: 3px; }
  .sheet--landscape .badge { width: 72px; height: 72px; border-width: 9px; border-radius: 16px; }
  .sheet--landscape .badge__icon { width: 34px; height: 34px; }
  .sheet--landscape .phase-tab { width: 188px; height: 43px; font-size: 29px; }
  .sheet--landscape .phase-card { width: 460px; height: 106px; border-radius: 53px; padding: 14px 30px 0 70px; }
  .sheet--landscape .phase-card p { font-size: 15.5px; line-height: 18px; }
  .sheet--landscape .phase-card b { font-size: 20px; }
  .sheet--landscape .phase-icon { width: 108px; height: 108px; border-width: 4px; }

  /* portrait sizing */
  .sheet--portrait .title-box { left: 40px; top: 82px; width: 306px; height: 38px; font-size: 17px; }
  .sheet--portrait .brand { left: 81px; top: 17px; gap: 8px; }
  .sheet--portrait .brand__dot { width: 42px; height: 42px; }
  .sheet--portrait .brand__name { font-size: 24px; }
  .sheet--portrait .area { width: 118px; height: 60px; border-radius: 30px; font-size: 10.5px; }
  .sheet--portrait .area small { font-size: 7px; margin-top: 2px; }
  .sheet--portrait .badge { width: 38px; height: 38px; border-width: 5px; border-radius: 9px; }
  .sheet--portrait .badge__icon { width: 18px; height: 18px; }
  .sheet--portrait .phase-tab { width: 86px; height: 18px; font-size: 12px; }
  .sheet--portrait .phase-card { width: 210px; height: 46px; border-radius: 23px; padding: 6px 10px 0 30px; }
  .sheet--portrait .phase-card p { font-size: 6.2px; line-height: 7.4px; }
  .sheet--portrait .phase-card b { font-size: 7.6px; }
  .sheet--portrait .phase-icon { width: 48px; height: 48px; border-width: 2px; }
</style>
</head>
<body>

<!-- Landscape 16:9 -->
<section class="sheet sheet--landscape">
  <h1 class="title-box abs">The 4 Dimensions of Transformation</h1>
  <div class="brand abs"><span class="brand__dot"></span><span class="brand__name">Brackwater Institute</span></div>

  <svg class="links" width="600" height="686" viewBox="0 0 600 686" aria-hidden="true">
    <ellipse cx="314" cy="280" rx="137" ry="122" fill="none" stroke="var(--accent)" stroke-width="4"/>
    <path d="M182 500 C 200 400, 260 370, 314 372 C 370 370, 430 400, 447 500" fill="none" stroke="var(--accent)" stroke-width="4"/>
  </svg>

  <div class="area area--peak" style="left:205px;top:225px;">Becoming Unlimited<small>The Peak</small></div>
  <div class="area area--heart" style="left:208px;top:420px;">Heart<br>Centered Living<small>The Bridge</small></div>
  <div class="area area--ground" style="left:73px;top:545px;">Embodiment<small>The Foundation</small></div>
  <div class="area area--lens" style="left:337px;top:545px;">Focus &amp;<br>Intuition Redefined<small>The Lens</small></div>

  <div class="badge" style="left:269px;top:140px;"><span class="badge__icon badge__icon--peak" role="img" aria-label="Icon: figure rising on a mountain top"></span></div>
  <div class="badge" style="left:269px;top:330px;"><span class="badge__icon badge__icon--heart" role="img" aria-label="Icon: people joined in an arch"></span></div>
  <div class="badge" style="left:137px;top:455px;"><span class="badge__icon badge__icon--ground" role="img" aria-label="Icon: seated meditating figure"></span></div>
  <div class="badge" style="left:402px;top:455px;"><span class="badge__icon badge__icon--lens" role="img" aria-label="Icon: eye with radiating lines"></span></div>

  <div class="method-line" style="left:725px;top:155px;width:5px;height:500px;"></div>

  <div class="phase-tab" style="left:733px;top:162px;">Phase 1</div>
  <div class="phase-card" style="left:730px;top:207px;"><p><b>Awareness &amp; Insight</b> –Cultivating self-reflection, identifying patterns, and gaining clarity on personal drivers through introspective practices and data-informed assessment.</p></div>
  <span class="phase-icon" style="left:673px;top:206px;" role="img" aria-label="Icon: head in profile with a light bulb"></span>

  <div class="phase-tab" style="left:733px;top:335px;">Phase 2</div>
  <div class="phase-card" style="left:730px;top:380px;"><p><b>Integration &amp; Practice</b> –Applying tools and frameworks, developing new habits, and aligning actions with core values through consistent application and feedback loops.</p></div>
  <span class="phase-icon" style="left:673px;top:379px;" role="img" aria-label="Icon: hand holding a gear with circular arrows"></span>

  <div class="phase-tab" style="left:733px;top:507px;">Phase 3</div>
  <div class="phase-card" style="left:730px;top:552px;"><p><b>Expansion &amp; Sustainable Growth</b> –Achieving long-term transformation, exceeding limitations, and fostering resilience through continuous evolution and a purpose-driven approach.</p></div>
  <span class="phase-icon" style="left:673px;top:551px;" role="img" aria-label="Icon: sprouting plant with rising arrow"></span>
</section>

<!-- Portrait / mobile -->
<section class="sheet sheet--portrait">
  <div class="brand abs"><span class="brand__dot"></span><span class="brand__name">Brackwater Institute</span></div>
  <h2 class="title-box abs">The 4 Dimensions of Transformation</h2>

  <svg class="links" width="386" height="440" viewBox="0 0 386 440" aria-hidden="true">
    <ellipse cx="193" cy="207" rx="73" ry="66" fill="none" stroke="var(--accent)" stroke-width="2.5"/>
    <path d="M122 333 C 132 280, 165 264, 193 265 C 222 264, 255 280, 265 333" fill="none" stroke="var(--accent)" stroke-width="2.5"/>
  </svg>

  <div class="area area--peak" style="left:134px;top:185px;">Becoming Unlimited<small>The Peak</small></div>
  <div class="area area--heart" style="left:134px;top:290px;">Heart<br>Centered Living<small>The Bridge</small></div>
  <div class="area area--ground" style="left:63px;top:358px;">Embodiment<small>The Foundation</small></div>
  <div class="area area--lens" style="left:206px;top:358px;">Focus &amp;<br>Intuition Redefined<small>The Lens</small></div>

  <div class="badge" style="left:174px;top:144px;"><span class="badge__icon badge__icon--peak" role="img" aria-label="Icon: figure rising on a mountain top"></span></div>
  <div class="badge" style="left:174px;top:246px;"><span class="badge__icon badge__icon--heart" role="img" aria-label="Icon: people joined in an arch"></span></div>
  <div class="badge" style="left:103px;top:314px;"><span class="badge__icon badge__icon--ground" role="img" aria-label="Icon: seated meditating figure"></span></div>
  <div class="badge" style="left:246px;top:314px;"><span class="badge__icon badge__icon--lens" role="img" aria-label="Icon: eye with radiating lines"></span></div>

  <div class="method-line" style="left:41px;top:443px;width:3px;height:220px;"></div>

  <div class="phase-tab" style="left:44px;top:447px;">Phase 1</div>
  <div class="phase-card" style="left:40px;top:467px;"><p><b>Awareness &amp; Insight</b> –Cultivating self-reflection, identifying patterns, and gaining clarity on personal drivers through introspective practices and data-informed assessment.</p></div>
  <span class="phase-icon" style="left:18px;top:466px;" role="img" aria-label="Icon: head in profile with a light bulb"></span>

  <div class="phase-tab" style="left:44px;top:525px;">Phase 2</div>
  <div class="phase-card" style="left:40px;top:545px;"><p><b>Integration &amp; Practice</b> –Applying tools and frameworks, developing new habits, and aligning actions with core values through consistent application and feedback loops.</p></div>
  <span class="phase-icon" style="left:18px;top:544px;" role="img" aria-label="Icon: hand holding a gear with circular arrows"></span>

  <div class="phase-tab" style="left:44px;top:603px;">Phase 3</div>
  <div class="phase-card" style="left:40px;top:623px;"><p><b>Expansion &amp; Sustainable Growth</b> –Achieving long-term transformation, exceeding limitations, and fostering resilience through continuous evolution and a purpose-driven approach.</p></div>
  <span class="phase-icon" style="left:18px;top:622px;" role="img" aria-label="Icon: sprouting plant with rising arrow"></span>
</section>

</body>
</html>
```